Business Cards for company that supports physicians that do medical research

Need to create a business card for Qorvel Studies (www.qorvelstudies.example), a company devoted to supporting physicians who conduct medical research. The form of the card should match the message of research and information quest. I have provided the logo of the company as an uploaded file. Designs should be simple and slick aimed at very high end clients.

Target Market(s)

Medical doctors that are also researchers

Industry/Entity Type

Medical

Contact Information for Business Card

Should feature logo and fields for personal info:
Name/title
Phone /email

Font styles to use
Serif
Sans Serif

Requirements
Must have
• Qorvel logo and fields for personal info:
• Name: Bertrand Okonfu
• Title: VP Research and Senior Analyst
• Phone: 555-203-4719
• email: info@qorvelstudies.example
Nice to have
• Interesting cards that I've seen:
• 1- all black/charcoal or very dark background
• 2- Plastic - semi-transparent
• 3- non-standard height-width ratios
• 4- Functional cards -- USB drive incorporated
Should not have
• Too busy; needs to stay very simple

```html
<!DOCTYPE html>
<html lang="en">
<head>
<meta charset="utf-8">
<title>Qorvel Studies — Business Card</title>
<link rel="stylesheet" href="https://fonts.googleapis.com/css2?family=Source+Sans+3:ital,wght@0,400;0,600;1,400&display=swap">
<style>
  :root {
    --backdrop: #3b3b3b;
    --card-white: #f7f7f7;
    --brand-blue: #1b7bbd;
    --brand-green: #45ae3c;
    --ink: #3d3d3d;
    --ink-soft: #4a4a4a;
    --on-blue: #ffffff;
  }
  * { box-sizing: border-box; margin: 0; padding: 0; }
  html, body {
    width: 1200px;
    height: 750px;
    overflow: hidden;
    background: var(--backdrop);
    font-family: "Source Sans 3", "Helvetica Neue", Arial, sans-serif;
  }
  .stage {
    position: relative;
    width: 1200px;
    height: 750px;
  }
  .card {
    position: absolute;
    top: 228px;
    width: 461px;
    height: 262px;
    overflow: hidden;
    background: var(--brand-blue);
  }
  .card--front { left: 124px; }
  .card--back { left: 618px; }

  .front-shape {
    position: absolute;
    inset: 0;
    width: 461px;
    height: 262px;
  }
  .front-content {
    position: absolute;
    left: 30px;
    top: 0;
  }
  .brand-name {
    position: absolute;
    left: 0;
    top: 52px;
    white-space: nowrap;
    font-size: 33px;
    font-weight: 600;
    line-height: 1;
    color: var(--brand-blue);
    letter-spacing: 0.2px;
  }
  .person-name {
    position: absolute;
    left: -1px;
    top: 141px;
    white-space: nowrap;
    font-size: 18px;
    font-weight: 600;
    color: var(--brand-green);
    line-height: 1;
  }
  .person-title {
    position: absolute;
    left: 1px;
    top: 163px;
    white-space: nowrap;
    font-size: 13px;
    color: var(--ink);
    line-height: 1;
  }
  .contact-list {
    position: absolute;
    left: 0;
    top: 188px;
    list-style: none;
  }
  .contact-item {
    display: flex;
    align-items: center;
    gap: 6px;
    height: 17.5px;
    font-size: 11.5px;
    color: var(--ink-soft);
    white-space: nowrap;
  }
  .contact-icon {
    width: 11px;
    height: 11px;
    flex: none;
  }

  .back-brand {
    position: absolute;
    right: 26px;
    top: 178px;
    text-align: right;
    color: var(--on-blue);
  }
  .back-brand__name {
    font-size: 30px;
    font-weight: 600;
    line-height: 1;
    white-space: nowrap;
  }
  .back-brand__web {
    margin-top: 14px;
    font-size: 10.5px;
    font-style: italic;
    letter-spacing: 1.2px;
    white-space: nowrap;
  }
</style>
</head>
<body>
<main class="stage">

  <section class="card card--front" aria-label="Business card front">
    <svg class="front-shape" viewBox="0 0 461 262" aria-hidden="true">
      <path fill="var(--brand-green)" d="M0 0 H353 C430 10 460 72 433 123 C401 185 302 238 181 262 H0 Z"/>
      <path fill="var(--card-white)" d="M0 0 H348 C420 10 450 70 425 120 C395 180 300 235 172 262 H0 Z"/>
    </svg>

    <div class="front-content">
      <div class="brand-name">Qorvel Studies</div>

      <div class="person-name">Bertrand Okonfu</div>
      <div class="person-title">VP Research &amp; Senior Analyst</div>

      <ul class="contact-list">
        <li class="contact-item">
          <svg class="contact-icon" viewBox="0 0 12 12" aria-hidden="true">
            <path fill="var(--brand-green)" d="M2.4 0.6 L4.3 2.9 L3.3 4.2 C3.9 5.6 5.2 7.2 7 8 L8.3 7 L10.8 8.8 L9.8 11 C5.3 10.9 1.1 6.6 0.8 1.9 Z"/>
          </svg>
          555-203-4719
        </li>
        <li class="contact-item">
          <svg class="contact-icon" viewBox="0 0 12 12" aria-hidden="true">
            <rect x="0.5" y="2.5" width="11" height="7.5" fill="var(--brand-green)"/>
            <path d="M0.8 2.8 L6 6.8 L11.2 2.8" fill="none" stroke="#ffffff" stroke-width="1"/>
          </svg>
          info@qorvelstudies.example
        </li>
        <li class="contact-item">
          <svg class="contact-icon" viewBox="0 0 12 12" aria-hidden="true">
            <circle cx="6" cy="6" r="5.5" fill="var(--brand-green)"/>
            <ellipse cx="6" cy="6" rx="2.3" ry="5.5" fill="none" stroke="#ffffff" stroke-width="0.8"/>
            <line x1="0.5" y1="6" x2="11.5" y2="6" stroke="#ffffff" stroke-width="0.8"/>
          </svg>
          www.qorvelstudies.example
        </li>
      </ul>
    </div>
  </section>

  <section class="card card--back" aria-label="Business card back">
    <div class="back-brand">
      <div class="back-brand__name">Qorvel Studies</div>
      <div class="back-brand__web">www.qorvelstudies.example</div>
    </div>
  </section>

</main>
</body>
</html>
```